Jolly Hounds Dog Behaviour, Training and Natural Healthcare Business Card Design

I am an experienced and qualified dog behavioural trainer and natural animal healthcare consultant offering a range of services to help pet dog owners with the "whole dog".
COLOURS: A soft light blue in the background - can be fading out or split, red should also feature
LOGO: Dog, healing hands, silhouette, shadow
SERVICES: Behaviour Consults, Training, Complex Skills Coaching Walking Coaching, Diet & Nutrition, Environmental Enrichment, Lifestyle and Lifestage Adaptations, Massage, Natural Health Options
BY LINE: Happy Dogs, Happy Owners
VALUES: Promoting communication and connection between dogs and their owners.
FOCUS: Nutritional guidance and environmental adaptation are often needed to complete the package and increase the success rate of training and behaviour modification.

Target Market(s)

Everyone who has a dog who they wish to improve their relationship with

Industry/Entity Type

Communication

Contact Information for Business Card

Jolly Hounds, Rebecca Thornbury, 0427 861350, jollyhounds7@fernpost.example, www.jollyhounds7.example, Qualified Dog Behavioural Trainer and Natural Animal Healthcare Consultant

Font styles to use
Sans Serif
Script

Colors
85cae6
ec2027

Requirements
Must have
• A clear indication that it is a dog services business. A raised feature
Should not have
• Pawprints, cartoons

```html
<!DOCTYPE html>
<html lang="en">
<head>
<meta charset="utf-8">
<title>Jolly Hounds – Business Card</title>
<link rel="stylesheet" href="https://fonts.googleapis.com/css2?family=Yesteryear&family=Ubuntu+Mono:wght@400;700&display=swap">
<style>
  :root {
    --stage: #2a2a2c;
    --sky-blue: #85cae6;
    --signal-red: #ec2027;
    --ink-black: #050505;
    --paper-white: #ffffff;
    --text-dark: #111111;
    --photo-leaf: #3f5a36;
    --photo-fur: #d9b98a;
    --photo-stone: #7d7a72;
  }
  * { margin: 0; padding: 0; box-sizing: border-box; }
  html, body {
    width: 1200px;
    height: 900px;
    overflow: hidden;
    background: var(--stage);
  }
  .canvas {
    width: 1200px;
    height: 900px;
    display: flex;
    align-items: center;
    justify-content: center;
  }
  .business-card {
    width: 1050px;
    height: 600px;
    box-shadow: 0 18px 40px rgba(0,0,0,0.55);
    background: var(--sky-blue);
  }
  .business-card svg { display: block; }
  .brand-name {
    font-family: "Yesteryear", cursive;
    font-size: 66px;
    fill: var(--paper-white);
  }
  .tagline {
    font-family: "Ubuntu Mono", monospace;
    font-size: 19px;
    fill: var(--paper-white);
  }
  .person-name {
    font-family: "Yesteryear", cursive;
    font-size: 46px;
    fill: var(--text-dark);
  }
  .contact-text {
    font-family: "Ubuntu Mono", monospace;
    font-size: 25px;
    fill: var(--text-dark);
  }
  .phone-number {
    font-family: "Ubuntu Mono", monospace;
    font-size: 30px;
    letter-spacing: 2px;
    fill: var(--text-dark);
  }
  .icon { fill: none; stroke: var(--text-dark); stroke-width: 2; }
</style>
</head>
<body>
<main class="canvas">
  <article class="business-card">
    <svg width="1050" height="600" viewBox="0 0 1050 600" xmlns="http://www.w3.org/2000/svg">
      <defs>
        <linearGradient id="photo-tones" x1="0" y1="0" x2="1" y2="1">
          <stop offset="0" stop-color="var(--photo-leaf)"/>
          <stop offset="0.45" stop-color="var(--photo-fur)"/>
          <stop offset="1" stop-color="var(--photo-stone)"/>
        </linearGradient>
        <clipPath id="header-clip">
          <path d="M0 0 H1050 V100 C900 150 650 285 0 312 Z"/>
        </clipPath>
      </defs>

      <!-- sky-blue base -->
      <rect class="card-base" width="1050" height="600" fill="var(--sky-blue)"/>

      <!-- swoosh layers -->
      <path class="swoosh-white-lower" d="M0 0 H1050 V180 C800 240 400 330 0 342 Z" fill="var(--paper-white)"/>
      <path class="swoosh-red" d="M0 0 H1050 V162 C820 215 500 300 0 326 Z" fill="var(--signal-red)"/>
      <path class="swoosh-white-upper" d="M0 0 H1050 V116 C900 162 650 292 0 318 Z" fill="var(--paper-white)"/>

      <!-- header: black field with photo area -->
      <g clip-path="url(#header-clip)">
        <rect class="header-field" width="1050" height="320" fill="var(--ink-black)"/>
        <rect class="photo-area" x="0" y="0" width="770" height="320" fill="url(#photo-tones)"
              role="img" aria-label="Photo of a happy dog looking up with its tongue out in a garden"/>
        <polygon class="title-band" points="250,0 1050,0 1050,128 250,128" fill="var(--ink-black)"/>
      </g>

      <!-- brand and tagline -->
      <text class="brand-name" x="640" y="66" text-anchor="middle">Jolly Hounds</text>
      <text class="tagline" x="650" y="94" text-anchor="middle">Qualified Dog Behavioural</text>
      <text class="tagline" x="650" y="116" text-anchor="middle">Trainer and Natural Animal Healthcare Consultant</text>

      <!-- person -->
      <text class="person-name" x="985" y="430" text-anchor="end">Rebecca Thornbury</text>
      <text class="phone-number" x="985" y="472" text-anchor="end">0427 861350</text>

      <!-- email -->
      <g class="email-icon" transform="translate(52,488)">
        <rect class="icon" x="0" y="0" width="22" height="16" rx="2"/>
        <path class="icon" d="M0 1 L11 9 L22 1"/>
      </g>
      <text class="contact-text" x="86" y="504">jollyhounds7@fernpost.example</text>

      <!-- website -->
      <g class="web-icon" transform="translate(462,548)">
        <circle class="icon" cx="10" cy="10" r="10"/>
        <ellipse class="icon" cx="10" cy="10" rx="4.5" ry="10"/>
        <path class="icon" d="M0 10 H20"/>
      </g>
      <text class="contact-text" x="494" y="566">www.jollyhounds7.example</text>
    </svg>
  </article>
</main>
</body>
</html>
```